PYLON SIGN FOR “MEADOWLARK CAR WASH SPRINT”

please see the new images in my brief. I have a logo design and the colors I would like you to follow.

please put "meadowlark car wash sprint" in the logo

Target Market(s)

GENERAL PUBLIC

Industry/Entity Type

CAR WASH

Font styles to use
Other font styles liked:
• CURSIVE AND BLOCK LETTERING BOTH AS IN THE SAMPLE PIC

Colors
00AB8E
00BBA5
67D7C9
C6EFE9
E9F9F6
6B429C
8869AF
B7A5CE
E3DAEB
F3F0F8

Requirements
Must have
• 1. “MEADOWLARK CAR WASH SPRINT” PLEASE PUT THIS IN THE LOGO 2. USE BLACK, WHITE, GREEN AND SILVER FOR A COLOR
Nice to have
• I WOULD LIKE TO SEE THE SIGN IN BOTH COLOR THEMES: WHITE, BLACK, GREEN AND SILVER AND WHITE BLACK PURPLE AND SILVER

```html
<!DOCTYPE html>
<html lang="en">
<head>
<meta charset="utf-8">
<title>Meadowlark Car Wash Sprint – Pylon Sign</title>
<link rel="stylesheet" href="https://fonts.googleapis.com/css2?family=Russo+One&display=swap">
<style>
  :root {
    --page-bg: #cfcfd1;
    --sign-bg: #061416;
    --sign-deep: #03090b;
    --green: #7cd11c;
    --green-light: #b6f03a;
    --green-dark: #1f5a0d;
    --teal-glow: #1fd6a0;
    --silver: #e4e6e8;
    --silver-dark: #9ea3a8;
    --road-navy: #151a3a;
    --road-purple: #2a1740;
  }
  * { margin: 0; padding: 0; box-sizing: border-box; }
  html, body {
    width: 830px;
    height: 1200px;
    overflow: hidden;
    background: var(--page-bg);
  }
  .canvas {
    position: relative;
    width: 830px;
    height: 1200px;
  }
  .sign {
    position: absolute;
    left: 20px;
    top: 298px;
    width: 790px;
    height: 605px;
    overflow: hidden;
    background: radial-gradient(ellipse at 50% 40%, #0b2326 0%, var(--sign-bg) 55%, var(--sign-deep) 100%);
    box-shadow: 0 6px 18px rgba(0, 0, 0, 0.35);
  }
  .light-streaks {
    position: absolute;
    inset: 0 0 157px 0;
    background:
      linear-gradient(135deg, rgba(31, 214, 160, 0.55) 0%, rgba(31, 214, 160, 0.18) 18%, transparent 34%),
      linear-gradient(225deg, rgba(31, 214, 160, 0.55) 0%, rgba(31, 214, 160, 0.18) 18%, transparent 34%),
      linear-gradient(180deg, rgba(20, 120, 130, 0.35) 0%, transparent 30%);
  }
  .road-scene {
    position: absolute;
    left: 0;
    right: 0;
    bottom: 0;
    height: 157px;
    background: linear-gradient(180deg, var(--road-navy) 0%, var(--road-purple) 60%, #120a1c 100%);
  }
  .brand-mark {
    position: absolute;
    left: 0;
    right: 0;
    top: 118px;
    text-align: center;
    font-family: "Russo One", sans-serif;
    color: var(--green);
    line-height: 1;
  }
  .brand-dot {
    display: block;
    width: 26px;
    height: 26px;
    margin: 0 auto 14px;
    border-radius: 50%;
    background: var(--green);
  }
  .brand-name {
    display: block;
    font-size: 50px;
  }
  .brand-tagline {
    display: block;
    margin-top: 10px;
    font-size: 17px;
    letter-spacing: 2px;
  }
  .headline {
    position: absolute;
    inset: 0;
    width: 790px;
    height: 605px;
    font-family: "Russo One", sans-serif;
  }
  .headline-line { font-size: 84px; }
  .headline-first { filter: drop-shadow(0 0 3px rgba(0, 0, 0, 0.8)); }
  .headline-middle,
  .headline-last { filter: drop-shadow(0 0 6px var(--green)); }
</style>
</head>
<body>
<main class="canvas">
  <section class="sign">
    <div class="light-streaks" role="img" aria-label="Green and teal light streaks fanning from the top corners"></div>
    <div class="road-scene" role="img" aria-label="Car driving on a neon grid road at night"></div>

    <div class="brand-mark">
      <span class="brand-dot"></span>
      <span class="brand-name">MEADOWLARK</span>
      <span class="brand-tagline">CAR WASH SPRINT</span>
    </div>

    <svg class="headline" viewBox="0 0 790 605" aria-label="Meadowlark Car Wash Sprint">
      <defs>
        <linearGradient id="green-fill" x1="0" y1="0" x2="0" y2="1">
          <stop offset="0" stop-color="#c4f545"/>
          <stop offset="0.5" stop-color="#7cd11c"/>
          <stop offset="1" stop-color="#3f9a10"/>
        </linearGradient>
        <linearGradient id="silver-fill" x1="0" y1="0" x2="0" y2="1">
          <stop offset="0" stop-color="#ffffff"/>
          <stop offset="0.5" stop-color="#c9cdd1"/>
          <stop offset="1" stop-color="#f2f3f4"/>
        </linearGradient>
        <linearGradient id="dark-green-fill" x1="0" y1="0" x2="0" y2="1">
          <stop offset="0" stop-color="#2a7a12"/>
          <stop offset="0.5" stop-color="#0d3a08"/>
          <stop offset="1" stop-color="#3c9b18"/>
        </linearGradient>
      </defs>
      <text class="headline-line headline-first" x="100" y="370" textLength="590" lengthAdjust="spacingAndGlyphs"
            fill="url(#green-fill)" stroke="#0a2a06" stroke-width="1.5">MEADOWLARK</text>
      <text class="headline-line headline-middle" x="122" y="448" textLength="545" lengthAdjust="spacingAndGlyphs"
            fill="url(#silver-fill)" stroke="#5fbf1a" stroke-width="2">CAR WASH</text>
      <text class="headline-line headline-last" x="165" y="533" textLength="460" lengthAdjust="spacingAndGlyphs"
            fill="url(#dark-green-fill)" stroke="#8fe52a" stroke-width="2">SPRINT</text>
    </svg>
  </section>
</main>
</body>
</html>
```